Finiding oppertunites in Real Estate 6.15.20

size of ad 7” x 9.6”
1-I like the ad to stand out and attract people's attention.
2-you should be able to see the text of the ad clearly .. see the attachment anything in yellow is instructions.
3-the list of topics should not be the main part of the ad
4-if you decide you want a picture or vector of a person .. (you decide)
then it should be a white male about 25-30 years old wearing a solid white or blue shirt and not long hair.
5-leave 1 inch for footer
see attachment
Good luck

Target Market(s)

potential male students 25-35 years of age

Industry/Entity Type

Education

Requirements
Must have
• will stand out and people would want to see it.
should be able to read the words of ad
Nice to have
• how to make money in real estate on one line

```html
<!DOCTYPE html>
<html lang="en">
<head>
<meta charset="utf-8">
<title>Real Estate Career Course</title>
<link rel="stylesheet" href="https://fonts.googleapis.com/css2?family=Cinzel:wght@700;800&family=Hind:wght@500;600&family=Roboto+Condensed:wght@700&family=Roboto:wght@500;700&display=swap">
<style>
  :root {
    --navy-deep: #1b2130;
    --navy-mid: #2a3850;
    --navy-light: #34445e;
    --white: #ffffff;
    --soft-white: #eef0f3;
    --ribbon-dark: #9c0b10;
    --ribbon-light: #ff4a4f;
    --burst-yellow: #faf000;
    --ink-navy: #1f3552;
    --footer-grey: #f2f1f1;
  }
  html, body { margin: 0; padding: 0; overflow: hidden; }
  body { width: 875px; height: 1200px; }
  .ad {
    position: relative;
    width: 875px;
    height: 1200px;
    overflow: hidden;
    background: linear-gradient(175deg, var(--navy-deep) 0%, var(--navy-mid) 45%, var(--navy-light) 62%, var(--navy-mid) 100%);
    color: var(--white);
  }
  .course-label {
    position: absolute; top: 36px; left: 0; width: 100%;
    margin: 0; text-align: center;
    font-family: 'Cinzel', serif; font-weight: 700; font-size: 34px;
    letter-spacing: 0.5px;
  }
  .headline {
    position: absolute; top: 122px; left: 0; width: 100%; margin: 0;
    font-family: 'Cinzel', serif; font-weight: 800;
    font-size: 62px; line-height: 70px; text-align: center;
    text-shadow: 0 0 18px rgba(255,255,255,0.25);
  }
  .headline-line { display: block; white-space: nowrap; }
  .headline-line--second { padding-left: 80px; }
  .house-icon { width: 60px; height: 60px; vertical-align: -4px; margin-left: 14px; }
  .divider {
    position: absolute; left: 150px; width: 575px; height: 6px;
    background: radial-gradient(ellipse at center, rgba(10,14,22,0.75) 0%, rgba(10,14,22,0) 70%);
  }
  .divider--top { top: 344px; }
  .divider--bottom { top: 548px; }
  .benefits { position: absolute; top: 378px; left: 169px; margin: 0; padding: 0; list-style: none; }
  .benefit {
    display: flex; align-items: center; height: 60px; margin-bottom: 28px;
    font-family: 'Hind', sans-serif; font-weight: 600; font-size: 29px; line-height: 29px;
    color: var(--soft-white);
  }
  .benefit-tick { width: 54px; height: 54px; flex: none; margin-right: 20px; }
  .ribbon { position: absolute; top: 632px; left: 112px; width: 540px; height: 126px; }
  .ribbon-text {
    position: absolute; top: 655px; left: 190px; width: 380px; text-align: center;
    font-family: 'Roboto Condensed', sans-serif; font-weight: 700; color: var(--white);
  }
  .ribbon-title { display: block; font-size: 38px; line-height: 42px; }
  .ribbon-sub { display: block; font-size: 29px; line-height: 34px; }
  .remote-badge { position: absolute; top: 582px; left: 606px; width: 218px; height: 218px; }
  .remote-label {
    position: absolute; top: 702px; left: 620px; width: 170px; text-align: center;
    font-family: 'Roboto', sans-serif; font-weight: 700; font-size: 19px; line-height: 20px;
    color: var(--ink-navy);
  }
  .topics {
    position: absolute; top: 838px; left: 197px; width: 479px; height: 99px;
    border: 2px solid var(--white); border-radius: 12px; box-sizing: border-box;
    text-align: center; font-family: 'Roboto', sans-serif;
  }
  .topics-title {
    position: absolute; top: -11px; left: 50%; transform: translateX(-50%);
    margin: 0; padding: 0 14px; white-space: nowrap;
    background: var(--navy-light);
    font-weight: 700; font-size: 16px; line-height: 20px;
  }
  .topics-list {
    margin: 19px 0 0; font-weight: 500; font-size: 14.5px; line-height: 18px; letter-spacing: 0.4px;
    white-space: nowrap;
  }
  .brand {
    position: absolute; top: 980px; left: 0; width: 100%;
    display: flex; justify-content: center; align-items: center; gap: 16px;
    font-family: 'Cinzel', serif; font-weight: 700; color: var(--white);
  }
  .brand-mark { width: 46px; height: 46px; background: var(--white); }
  .brand-name { font-size: 36px; line-height: 36px; }
  .footer-space {
    position: absolute; top: 1080px; left: 19px; width: 836px; height: 102px;
    background: var(--footer-grey);
  }
</style>
</head>
<body>
<main class="ad">
  <p class="course-label">Real Estate Career Course</p>

  <h1 class="headline">
    <span class="headline-line">How to Make Money</span>
    <span class="headline-line headline-line--second">In Real Estate?<svg class="house-icon" viewBox="0 0 60 60" aria-hidden="true"><path d="M4 28 L30 6 L56 28" fill="none" stroke="#fff" stroke-width="6" stroke-linejoin="miter"/><path d="M12 30 L30 15 L48 30 L48 58 M12 58 L12 30" fill="none" stroke="#fff" stroke-width="6"/><rect x="24" y="36" width="5" height="5" fill="#fff"/><rect x="31" y="36" width="5" height="5" fill="#fff"/><rect x="24" y="43" width="5" height="5" fill="#fff"/><rect x="31" y="43" width="5" height="5" fill="#fff"/></svg></span>
  </h1>

  <div class="divider divider--top"></div>

  <ul class="benefits">
    <li class="benefit">
      <svg class="benefit-tick" viewBox="0 0 54 54" aria-hidden="true"><circle cx="27" cy="27" r="23" fill="none" stroke="#eef0f3" stroke-width="6"/><path d="M17 27 L24 34 L37 20" fill="none" stroke="#eef0f3" stroke-width="6" stroke-linecap="round" stroke-linejoin="round"/></svg>
      <span>For those who have started or<br>would like to go into Real Estate</span>
    </li>
    <li class="benefit">
      <svg class="benefit-tick" viewBox="0 0 54 54" aria-hidden="true"><circle cx="27" cy="27" r="23" fill="none" stroke="#eef0f3" stroke-width="6"/><path d="M17 27 L24 34 L37 20" fill="none" stroke="#eef0f3" stroke-width="6" stroke-linecap="round" stroke-linejoin="round"/></svg>
      <span>An investment in knowledge opens<br>up untold opportunities</span>
    </li>
  </ul>

  <div class="divider divider--bottom"></div>

  <svg class="ribbon" viewBox="0 0 540 126" aria-hidden="true">
    <defs>
      <linearGradient id="ribbonBand" x1="0" x2="1" y1="0" y2="0">
        <stop offset="0" stop-color="#9c0b10"/>
        <stop offset="1" stop-color="#ff4a4f"/>
      </linearGradient>
    </defs>
    <path d="M2 4 L48 56 L28 88 Z" fill="#c5141b"/>
    <path d="M18 22 Q20 18 40 18 L490 18 Q530 22 535 52 L540 120 L505 68 Q470 104 420 104 L60 104 Q30 104 20 70 Z" fill="url(#ribbonBand)"/>
    <path d="M510 70 L540 122 L535 52 Z" fill="#e0262c"/>
  </svg>
  <p class="ribbon-text">
    <span class="ribbon-title">12 Session Course</span>
    <span class="ribbon-sub">Classes Starting June 16</span>
  </p>

  <svg class="remote-badge" viewBox="0 0 218 218" aria-hidden="true">
    <polygon fill="#faf000" points="109,0 122,31 146,6 148,40 179,24 169,57 205,52 182,80 216,89 186,109 216,129 182,138 205,166 169,161 179,194 148,178 146,212 122,187 109,218 96,187 72,212 70,178 39,194 49,161 13,166 36,138 2,129 32,109 2,89 36,80 13,52 49,57 39,24 70,40 72,6 96,31"/>
    <rect x="66" y="60" width="64" height="44" rx="3" fill="none" stroke="#1f3552" stroke-width="7"/>
    <rect x="92" y="104" width="12" height="10" fill="#1f3552"/>
    <rect x="80" y="113" width="36" height="5" fill="#1f3552"/>
    <rect x="110" y="44" width="34" height="26" rx="6" fill="#faf000" stroke="#1f3552" stroke-width="5"/>
    <path d="M116 70 L114 80 L124 70" fill="#1f3552"/>
    <line x1="118" y1="52" x2="136" y2="52" stroke="#1f3552" stroke-width="3"/>
    <line x1="118" y1="58" x2="136" y2="58" stroke="#1f3552" stroke-width="3"/>
  </svg>
  <p class="remote-label">REMOTE<br>SESSIONS</p>

  <section class="topics">
    <h2 class="topics-title">A PARTIAL LISTING OF TOPICS</h2>
    <p class="topics-list">
      Single-family | Multifamily | Management | Real Estate Concepts<br>
      Real Estate law | Investment properties | Foreclosures | Rehab<br>
      Foreclosures | Short sales | Development | Finical modeling<br>
      HUD properties | Due Diligencene
    </p>
  </section>

  <div class="brand">
    <span class="brand-mark"></span>
    <span class="brand-name">HARBORLINE<br>CAPITAL GROUP</span>
  </div>

  <div class="footer-space"></div>
</main>
</body>
</html>
```